Local Roofing/Construction company business needs new biz card design

We need a new business card design, current cards are from the start of this operation and generic at best. We are a local Construction Company (General Contractor) with a majority of our work originating from insurance claims-exterior finish work is the main focus (Roofs-Siding-Gutters etc). Heavily involved with homeowners and the low ball offers they receive from insurance company's after a insurable event takes place. I have attached some of our original logo file(s) below.

```html
<!DOCTYPE html>
<html lang="en">
<head>
<meta charset="utf-8">
<title>Halvern Construction – Business Card</title>
<link rel="stylesheet" href="https://fonts.googleapis.com/css2?family=Poppins:wght@400;500;700;800&display=swap">
<style>
  :root {
    --stage: #2a2a2a;
    --card-dark: #2e2e2e;
    --card-light: #ffffff;
    --brand-green: #2fd777;
    --ink: #2b2b2b;
    --divider: #d9d9d9;
  }
  * { box-sizing: border-box; margin: 0; padding: 0; }
  html, body {
    width: 1200px; height: 689px; overflow: hidden;
    background: var(--stage);
    font-family: "Poppins", sans-serif;
  }
  .stage {
    position: relative; width: 1200px; height: 689px;
    display: flex; align-items: center; justify-content: center; gap: 60px;
  }
  .card {
    width: 520px; height: 298px; border-radius: 18px;
    position: relative; overflow: hidden;
    box-shadow: 0 18px 40px rgba(0,0,0,.45);
  }
  /* Back side */
  .card--back {
    background: var(--card-dark);
    display: flex; align-items: center; justify-content: center;
  }
  .brand-lockup {
    display: flex; align-items: center; gap: 14px;
  }
  .brand-square {
    width: 34px; height: 34px; background: var(--brand-green);
  }
  .brand-name {
    color: var(--brand-green); font-weight: 800;
    font-size: 30px; line-height: 1.05; letter-spacing: .5px;
    text-transform: uppercase;
  }
  .brand-name small { display: block; font-size: 30px; font-weight: 800; }
  /* Front side */
  .card--front {
    background: var(--card-light);
    display: grid; grid-template-columns: 250px 1px 1fr; align-items: center;
  }
  .front-brand {
    display: flex; flex-direction: column; align-items: center; gap: 14px;
  }
  .front-brand .brand-square { width: 46px; height: 46px; }
  .front-brand .brand-name { font-size: 26px; text-align: center; }
  .front-brand .brand-name small { font-size: 26px; }
  .divider { width: 1px; height: 190px; background: var(--divider); }
  .contact { padding-left: 28px; color: var(--ink); }
  .person-name {
    color: var(--brand-green); font-weight: 700; font-size: 21px;
    text-transform: uppercase; letter-spacing: .3px; line-height: 1.1;
  }
  .person-role { font-size: 13px; margin-bottom: 16px; }
  .contact-list { list-style: none; font-size: 12.5px; line-height: 1.55; }
  .contact-list li { display: flex; align-items: flex-start; gap: 8px; }
  .contact-list li.address { margin-top: 10px; line-height: 1.3; }
  .icon { width: 12px; height: 12px; flex: none; margin-top: 4px; fill: var(--brand-green); }
</style>
</head>
<body>
<main class="stage">
  <section class="card card--back" aria-label="Card back">
    <div class="brand-lockup">
      <span class="brand-square"></span>
      <p class="brand-name">Halvern<small>Construction</small></p>
    </div>
  </section>

  <section class="card card--front" aria-label="Card front">
    <div class="front-brand">
      <span class="brand-square"></span>
      <p class="brand-name">Halvern<small>Construction</small></p>
    </div>
    <span class="divider"></span>
    <div class="contact">
      <h1 class="person-name">Dorian Hale</h1>
      <p class="person-role">Managing Director</p>
      <ul class="contact-list">
        <li><svg class="icon" viewBox="0 0 24 24"><path d="M6.6 10.8a15 15 0 006.6 6.6l2.2-2.2c.3-.3.7-.4 1-.2 1.1.4 2.3.6 3.6.6.6 0 1 .4 1 1V20c0 .6-.4 1-1 1A17 17 0 013 4c0-.6.4-1 1-1h3.5c.6 0 1 .4 1 1 0 1.3.2 2.5.6 3.6.1.3 0 .7-.2 1z"/></svg>044-123 456 789</li>
        <li><svg class="icon" viewBox="0 0 24 24"><path d="M2 5h20v14H2z M2 5l10 8 10-8" fill="none" stroke="#2fd777" stroke-width="2.5"/></svg>info@email.com</li>
        <li><svg class="icon" viewBox="0 0 24 24"><circle cx="12" cy="12" r="9" fill="none" stroke="#2fd777" stroke-width="2.5"/><path d="M3 12h18M12 3c3 3 3 15 0 18M12 3c-3 3-3 15 0 18" fill="none" stroke="#2fd777" stroke-width="2"/></svg>www.website.com</li>
        <li class="address"><svg class="icon" viewBox="0 0 24 24"><path d="M12 2a7 7 0 00-7 7c0 5 7 13 7 13s7-8 7-13a7 7 0 00-7-7zm0 9.5A2.5 2.5 0 1112 6.5a2.5 2.5 0 010 5z"/></svg><span>123, 7th street<br>Country name, 123456</span></li>
      </ul>
    </div>
  </section>
</main>
</body>
</html>
```